Personal Injury Lawyer Billboard

I would like a design created featuring the image of the lawyer centered in the middle of the design.
To the left of the lawyer's image it should read "INJURED?"
To the right of the lawyer's image, it should read "CALL DEAN!"
Under Call Dean, include the phone number 318-555-0187.
At the bottom of the design include the lawyers information "Dean Marlowe Accident & Injury Lawyers"
PLEASE REMOVED THE BACKGROUND IMAGERY OF THE PHOTO SUBMITTED. Also, the colors for this design should match the colors shown in the logo (navy, white and relective soft gold). Please use those color combinations in ways that best stand out.

```html
<!DOCTYPE html>
<html lang="en">
<head>
<meta charset="utf-8">
<title>Dean Marlowe Accident &amp; Injury Lawyers — Billboard</title>
<link href="https://fonts.googleapis.com/css2?family=Old+Standard+TT:wght@700&family=Oswald:wght@500&display=swap" rel="stylesheet">
<style>
  :root {
    --navy: #0c1f4d;
    --navy-deep: #091840;
    --gold-dark: #c49a2e;
    --gold-light: #ead56c;
    --gold-line: #d9ac3a;
    --white: #ffffff;
    --page: #eef0f3;
  }
  html, body {
    margin: 0;
    width: 1200px;
    height: 1200px;
    overflow: hidden;
    background: var(--page);
  }
  .billboard {
    position: absolute;
    left: 40px;
    top: 437px;
    width: 1120px;
    height: 326px;
    overflow: hidden;
    background: linear-gradient(90deg, var(--gold-dark) 0%, var(--gold-light) 22%, var(--gold-light) 34%, var(--gold-dark) 55%);
    box-shadow: 0 10px 30px rgba(0,0,0,0.18);
  }
  .billboard__panels {
    position: absolute;
    inset: 0;
  }
  .headline-question {
    position: absolute;
    left: 18px;
    top: 128px;
    margin: 0;
    white-space: nowrap;
    font-family: "Old Standard TT", Georgia, serif;
    font-weight: 700;
    font-size: 84px;
    line-height: 1;
    color: var(--navy);
    letter-spacing: -2px;
    transform: scaleX(0.78);
    transform-origin: left center;
  }
  .lawyer-photo {
    position: absolute;
    left: 378px;
    top: 46px;
    width: 232px;
    height: 280px;
    background: linear-gradient(180deg, #b08a6e 0%, #8a6a55 28%, #1d2a5c 40%, #14204f 100%);
    border-radius: 100px 100px 0 0;
  }
  .call-out {
    position: absolute;
    left: 640px;
    top: 26px;
    width: 460px;
    text-align: center;
    font-family: "Old Standard TT", Georgia, serif;
    font-weight: 700;
    color: var(--white);
  }
  .call-out__line {
    margin: 0;
    white-space: nowrap;
    font-size: 62px;
    line-height: 1;
    letter-spacing: -1px;
  }
  .call-out__name { color: var(--gold-light); }
  .call-out__phone {
    margin: 6px 0 0;
    white-space: nowrap;
    font-size: 70px;
    line-height: 1;
    letter-spacing: -2px;
    transform: scaleX(0.9);
  }
  .call-out__rule {
    height: 1.5px;
    background: var(--white);
    margin: 12px 6px 0;
  }
  .firm {
    position: absolute;
    left: 740px;
    top: 210px;
    width: 260px;
    text-align: center;
    font-family: "Oswald", "Arial Narrow", sans-serif;
    font-weight: 500;
    color: var(--white);
  }
  .firm__name {
    margin: 0;
    white-space: nowrap;
    font-size: 32px;
    line-height: 1;
    letter-spacing: 0.5px;
  }
  .firm__tagline {
    margin: 6px 0 0;
    padding: 4px 0;
    white-space: nowrap;
    font-size: 16px;
    line-height: 1;
    border-top: 1.5px solid var(--gold-line);
    border-bottom: 1.5px solid var(--gold-line);
  }
</style>
</head>
<body>
  <section class="billboard" aria-label="Dean Marlowe Accident and Injury Lawyers billboard">
    <svg class="billboard__panels" width="1120" height="326" viewBox="0 0 1120 326" aria-hidden="true">
      <polygon points="552,0 1120,0 1120,326 580,326 624,163" fill="var(--gold-line)"/>
      <polygon points="564,0 1120,0 1120,326 592,326 636,163" fill="var(--navy)"/>
      <polygon points="540,0 552,0 612,163 568,326 556,326 600,163" fill="var(--navy-deep)"/>
    </svg>

    <h1 class="headline-question">INJURED?</h1>

    <div class="lawyer-photo" role="img" aria-label="Photo of the lawyer in a navy suit and green tie, smiling with a raised fist, background removed"></div>

    <div class="call-out">
      <p class="call-out__line">CALL <span class="call-out__name">DEAN!</span></p>
      <p class="call-out__phone">318-555-0187</p>
      <div class="call-out__rule"></div>
    </div>

    <div class="firm">
      <p class="firm__name">DEAN MARLOWE</p>
      <p class="firm__tagline">ACCIDENT &amp; INJURY LAWYERS</p>
    </div>
  </section>
</body>
</html>
```